Coastline Premier Retreats Business Card Design

Design a business card for Coastline Premier Retreats. Look at the website for colors and reference. Card should have logo, name, title, office number, mobile number, email, URL and a tagline like, "Luxury Hotel & Resort Email Marketing" (This might change).

https://www.coastlinepremierretreats.example

The rest I will leave up to your imagination.

Contact Information for Business Card

Logo, name, title, office number, mobile number, email, URL and a tagline like, "Luxury Hotel & Resort Email Marketing" (This might change).

```html
<!DOCTYPE html>
<html lang="en">
<head>
<meta charset="utf-8">
<title>Coastline Premier Retreats – Business Card</title>
<link rel="stylesheet" href="https://fonts.googleapis.com/css2?family=Arimo:wght@400;700&display=swap">
<style>
  :root {
    --orange: #f07522;
    --ink: #1c1c1c;
    --paper: #ffffff;
    --backdrop: #e6e3df;
  }
  * { box-sizing: border-box; margin: 0; padding: 0; }
  html, body {
    width: 1200px; height: 900px; overflow: hidden;
    background: var(--backdrop);
    font-family: "Arimo", Arial, sans-serif;
  }
  .canvas {
    width: 1200px; height: 900px;
    display: flex; flex-direction: column;
    align-items: center; justify-content: center; gap: 36px;
  }
  .card {
    position: relative;
    width: 700px; height: 400px;
    border-radius: 26px;
    overflow: hidden;
    box-shadow: 0 10px 24px rgba(0,0,0,.25);
  }
  .card--back {
    background: var(--orange);
    display: flex; align-items: center; justify-content: center;
  }
  .brand-name {
    font-weight: 700;
    text-transform: uppercase;
    letter-spacing: .06em;
    text-align: center;
    line-height: 1.1;
  }
  .card--back .brand-name { color: var(--paper); font-size: 44px; }
  .card--front { background: var(--paper); }
  .front-logo {
    position: absolute; left: 40px; top: 116px; width: 260px;
  }
  .card--front .brand-name { color: var(--ink); font-size: 26px; }
  .divider {
    position: absolute; left: 330px; top: 70px;
    width: 2px; height: 200px; background: var(--orange);
  }
  .details {
    position: absolute; left: 352px; top: 48px;
    color: var(--ink);
    z-index: 1;
  }
  .person-name {
    color: var(--orange); font-weight: 700; font-size: 27px;
    letter-spacing: .01em; margin-bottom: 6px;
  }
  .role { font-size: 16px; line-height: 1.35; }
  .contacts { list-style: none; margin-top: 10px; }
  .contacts li {
    display: flex; align-items: center; gap: 9px;
    font-size: 15px; line-height: 1.6;
  }
  .contacts svg { width: 15px; height: 15px; flex: none; }
  .wave { position: absolute; left: 0; bottom: 0; width: 700px; height: 140px; }
</style>
</head>
<body>
<main class="canvas">
  <section class="card card--back">
    <div class="brand-name">Coastline<br>Premier Retreats</div>
  </section>

  <section class="card card--front">
    <div class="front-logo">
      <div class="brand-name">Coastline<br>Premier Retreats</div>
    </div>
    <div class="divider"></div>
    <div class="details">
      <h1 class="person-name">DANIEL MARLOWE</h1>
      <p class="role">Co-Founder</p>
      <p class="role">Luxury Hotel &amp; Resort</p>
      <p class="role">Email Marketing</p>
      <ul class="contacts">
        <li>
          <svg viewBox="0 0 16 16"><path fill="var(--orange)" d="M2 6c0-2 3-3 6-3s6 1 6 3v1h-3V6H5v1H2zM4 8h8l1 5H3z"/></svg>
          555-014-2297
        </li>
        <li>
          <svg viewBox="0 0 16 16"><rect x="4" y="1" width="8" height="14" rx="2" fill="none" stroke="var(--orange)" stroke-width="1.6"/><circle cx="8" cy="12.3" r="1" fill="var(--orange)"/></svg>
          555-016-3381
        </li>
        <li>
          <svg viewBox="0 0 16 16"><rect x="1" y="3" width="14" height="10" fill="var(--orange)"/><path d="M1 3l7 6 7-6" fill="none" stroke="#fff" stroke-width="1.3"/></svg>
          info@coastlinepremierretreats.example
        </li>
        <li>
          <svg viewBox="0 0 16 16"><circle cx="8" cy="8" r="7" fill="var(--orange)"/><path d="M1 8h14M8 1c-3 3-3 11 0 14M8 1c3 3 3 11 0 14" fill="none" stroke="#fff" stroke-width="1"/></svg>
          www.coastlinepremierretreats.example
        </li>
      </ul>
    </div>
    <svg class="wave" viewBox="0 0 700 140" preserveAspectRatio="none" aria-hidden="true">
      <path d="M0 125 C180 125 320 100 440 70 C540 45 620 30 700 26 L700 140 L0 140 Z" fill="var(--orange)"/>
      <path d="M0 116 C180 116 320 91 440 61 C540 36 620 21 700 17" fill="none" stroke="var(--ink)" stroke-width="5"/>
    </svg>
  </section>
</main>
</body>
</html>
```